Corvane Holdings , new business card design

investment firm with corporate clients . need double sided business card , vertical and horizontal options ,logo must be clear. prefer pantone colors only and sharp design. website also www.corvane.ae

Khalid Bin Tarrafi
Managing Director
Tel. +971 4 387 2940
Mobile +971 50 518 2403
khalid@corvane.ae
Q-Span Plaza, officw 18-B07, Warqa Gardens, Dubai

Contact Information for Business Card

Khalid Bin Tarrafi
Managing Director

Font styles to use
Serif

Colors

Designer to choose colors to be used in the design.

```html
<!DOCTYPE html>
<html lang="en">
<head>
<meta charset="utf-8">
<title>Corvane Holdings – Business Card</title>
<link href="https://fonts.googleapis.com/css2?family=Roboto:wght@300;400;700&display=swap" rel="stylesheet">
<style>
  :root {
    --backdrop: #e9e7e4;
    --card: #ffffff;
    --brand-blue: #4f76a0;
    --brand-blue-light: #6b90b8;
    --ink: #2b2d31;
    --ink-soft: #5a5d63;
    --white: #ffffff;
  }
  * { margin: 0; padding: 0; box-sizing: border-box; }
  html, body {
    width: 1200px; height: 911px; overflow: hidden;
    background: var(--backdrop);
    font-family: "Roboto", Arial, sans-serif;
  }
  .stage {
    position: relative; width: 1200px; height: 911px;
    display: flex; justify-content: center; align-items: center; gap: 60px;
  }
  .card {
    position: relative; width: 420px; height: 686px;
    background: var(--card);
    box-shadow: 0 6px 22px rgba(0,0,0,.18);
    overflow: hidden;
  }
  /* Front */
  .card-front__panel {
    position: absolute; left: 0; top: 0; width: 100%; height: 440px;
    background: linear-gradient(100deg, var(--brand-blue) 0%, var(--brand-blue-light) 55%, var(--brand-blue) 100%);
  }
  .holder { position: absolute; left: 120px; top: 70px; }
  .holder__name {
    color: var(--white); font-weight: 700; font-size: 19px; letter-spacing: .2px;
    text-transform: uppercase;
  }
  .holder__title {
    color: var(--ink); font-weight: 700; font-size: 14px; letter-spacing: .4px;
    text-transform: uppercase; margin-top: 2px; padding-left: 8px;
  }
  .contact {
    position: absolute; left: 90px; top: 190px;
    list-style: none; color: var(--white); font-size: 15px; line-height: 23px; letter-spacing: .3px;
  }
  .contact li:nth-child(2) { padding-left: 0; }
  .contact .gap { margin-top: 8px; }
  .wordmark {
    display: flex; align-items: center; gap: 12px;
    color: var(--ink); font-weight: 300; letter-spacing: 4px; text-transform: uppercase;
  }
  .wordmark__square { width: 14px; height: 14px; background: var(--brand-blue); flex: none; }
  .card-front .wordmark { position: absolute; left: 34px; top: 485px; font-size: 24px; }
  .address {
    position: absolute; left: 34px; top: 555px;
    color: var(--ink-soft); font-size: 15px; line-height: 22px; letter-spacing: .3px;
  }
  /* Back */
  .card-back .brand-block { position: absolute; right: 34px; bottom: 70px; text-align: right; }
  .card-back .wordmark { font-size: 24px; justify-content: flex-end; }
  .brand-block__web {
    margin-top: 12px; color: var(--ink); font-size: 13px; font-weight: 700; letter-spacing: 5px;
  }
</style>
</head>
<body>
<main class="stage">
  <section class="card card-front" aria-label="Business card front">
    <div class="card-front__panel"></div>
    <div class="holder">
      <p class="holder__name">Khalid Bin Tarrafi</p>
      <p class="holder__title">Managing Director</p>
    </div>
    <ul class="contact">
      <li>Phone : +971 4 387 2940</li>
      <li>Cell : +971 50 518 2403</li>
      <li class="gap">khalid@corvane.ae</li>
      <li>www.corvane.ae</li>
    </ul>
    <div class="wordmark"><span class="wordmark__square"></span>Corvane Holdings</div>
    <p class="address">Q-Span Plaza, officw 18-B07<br>Warqa Gardens, Dubai</p>
  </section>

  <section class="card card-back" aria-label="Business card back">
    <div class="brand-block">
      <div class="wordmark"><span class="wordmark__square"></span>Corvane Holdings</div>
      <p class="brand-block__web">www.corvane.ae</p>
    </div>
  </section>
</main>
</body>
</html>
```